Business cards to launch an education platform

Hi,
I am looking at having new business cards designed.
I am a startup, developing a web platform for schools and university, the education world. It's an online assessment system.
I would like a card that looks classy, and that is using the colors and the font of my logo.

I have attached:
1) my logo
2) A business card that I have designed quickly so you can have all the information required in the card, but I really don't like it.
3) The font that I am using (Lato Regular) to design my web platform
4) Some screenshots of my web platform so you can have a look at the style that I have.

Target Market(s)

Major market: Education system: Schools and university
Minor markets: Business in general

Industry/Entity Type

Business

Contact Information for Business Card

Clara Fenwick
Director

M: 0437 518 902
E: clara.fenwick@amberLoomSystems.com.au

Requirements
Must have
• The colors of my logo

```html
<!DOCTYPE html>
<html lang="en">
<head>
<meta charset="utf-8">
<title>Amber Loom Systems – Business Cards</title>
<link rel="stylesheet" href="https://fonts.googleapis.com/css2?family=Lato:wght@400;700&display=swap">
<style>
  :root {
    --page-bg: #e9ebee;
    --card-white: #f7f8f8;
    --navy: #14508f;
    --navy-deep: #0f3f76;
    --navy-light: #1d64a8;
    --cyan: #2fb8dc;
    --ink-white: #ffffff;
    --logo-blue: #1a5c9c;
  }
  * { margin: 0; padding: 0; box-sizing: border-box; }
  html, body {
    width: 1200px; height: 780px; overflow: hidden;
    background: var(--page-bg);
    font-family: "Lato", sans-serif;
  }
  .canvas {
    position: relative; width: 1200px; height: 780px;
    display: flex; align-items: center; justify-content: center; gap: 60px;
  }
  .card {
    position: relative; width: 520px; height: 298px;
    border-radius: 3px; overflow: hidden;
    box-shadow: 0 10px 28px rgba(20, 40, 70, .22), 0 2px 5px rgba(20, 40, 70, .18);
  }
  .card--front { background: var(--card-white); }
  .card--back {
    background: radial-gradient(ellipse at 45% 40%, var(--navy-light) 0%, var(--navy) 55%, var(--navy-deep) 100%);
  }
  .front-wave { position: absolute; inset: 0; width: 100%; height: 100%; }

  .brand { position: absolute; display: flex; align-items: center; gap: 14px; }
  .brand__mark { width: 46px; height: 46px; flex: none; }
  .brand__name {
    font-weight: 400; letter-spacing: 2.5px; text-transform: uppercase;
    line-height: 1.15; white-space: nowrap;
  }

  .card--front .brand { left: 34px; top: 44px; }
  .card--front .brand__mark { background: var(--logo-blue); }
  .card--front .brand__name { color: var(--logo-blue); font-size: 20px; }

  .card--back .brand { left: 50%; top: 50%; transform: translate(-50%, -50%); }
  .card--back .brand__mark { background: var(--ink-white); }
  .card--back .brand__name { color: var(--ink-white); font-size: 26px; }

  .contact { position: absolute; left: 40px; bottom: 22px; color: var(--ink-white); }
  .contact__name { font-size: 21px; font-weight: 700; line-height: 1.1; }
  .contact__role { font-size: 13px; opacity: .92; margin-bottom: 9px; }
  .contact__line { display: flex; align-items: center; gap: 8px; font-size: 12.5px; line-height: 1.7; }
  .contact__icon { width: 13px; height: 13px; flex: none; }
</style>
</head>
<body>
<main class="canvas">

  <section class="card card--front" aria-label="Business card front">
    <svg class="front-wave" viewBox="0 0 520 298" preserveAspectRatio="none" aria-hidden="true">
      <path d="M0,140 C140,136 260,100 330,52 C370,24 392,8 404,0 L520,0 L520,298 L0,298 Z" fill="#2fb8dc"/>
      <path d="M0,153 C146,149 270,113 341,65 C382,36 406,15 421,0 L520,0 L520,298 L0,298 Z" fill="#14508f"/>
      <path d="M0,149 C144,145 266,109 337,61 C377,33 400,13 414,0" fill="none" stroke="#f7f8f8" stroke-width="2.5"/>
    </svg>

    <div class="brand">
      <span class="brand__mark"></span>
      <span class="brand__name">Amber Loom<br>Systems</span>
    </div>

    <div class="contact">
      <p class="contact__name">Clara Fenwick</p>
      <p class="contact__role">Director</p>
      <p class="contact__line">
        <svg class="contact__icon" viewBox="0 0 13 13" aria-hidden="true">
          <rect x="0" y="0" width="13" height="13" rx="2" fill="#ffffff"/>
          <rect x="4" y="2" width="5" height="9" rx="1" fill="#14508f"/>
        </svg>
        0437 518 902
      </p>
      <p class="contact__line">
        <svg class="contact__icon" viewBox="0 0 13 13" aria-hidden="true">
          <rect x="0" y="0" width="13" height="13" rx="2" fill="#ffffff"/>
          <path d="M2.5,4 L10.5,4 L10.5,9.5 L2.5,9.5 Z M2.5,4 L6.5,7 L10.5,4" fill="none" stroke="#14508f" stroke-width="1.1"/>
        </svg>
        clara.fenwick@amberLoomSystems.com.au
      </p>
    </div>
  </section>

  <section class="card card--back" aria-label="Business card back">
    <div class="brand">
      <span class="brand__mark"></span>
      <span class="brand__name">Amber Loom Systems</span>
    </div>
  </section>

</main>
</body>
</html>
```